Home Security Company Business Card

Looking for a eye catching business card that is non traditional and stands out but yet still looks professional. It should include all the pertinent information such as name, title, address, telephone, e-mail, website address should definitely stand out and then finally the logo.

Target Market(s)

Residential and Commercial accounts mostly upscale accounts

Industry/Entity Type

Security

Contact Information for Business Card

Name
Title
Address
Office #
Cell #
E-mail
Website

Font styles to use
Serif
Sans Serif

Requirements
Must have
• Logo, two sided color configuration
Nice to have
• You decide
Should not have
• There really aren't any.

```html
<!DOCTYPE html>
<html lang="en">
<head>
<meta charset="utf-8">
<title>Hallmoor Security Systems – Business Card</title>
<link rel="stylesheet" href="https://fonts.googleapis.com/css2?family=Open+Sans:wght@400;600;700&display=swap">
<style>
  :root {
    --bg: #e9e4de;
    --maroon: #8a1d2b;
    --maroon-deep: #6a1420;
    --copper: #b4562f;
    --copper-light: #c8703f;
    --gold: #f0b43a;
    --gold-soft: #e6a632;
    --white: #ffffff;
    --paper: #fbfbfb;
    --rule: rgba(255,255,255,0.75);
  }
  * { box-sizing: border-box; margin: 0; padding: 0; }
  html, body { width: 1200px; height: 913px; overflow: hidden; }
  body {
    background: var(--bg);
    font-family: "Open Sans", Arial, sans-serif;
    position: relative;
  }
  .card {
    position: absolute;
    width: 540px;
    height: 310px;
    border-radius: 22px;
    overflow: hidden;
    box-shadow: 0 10px 26px rgba(0,0,0,0.22);
  }
  /* ---------- Front ---------- */
  .card-front {
    left: 40px; top: 300px;
    background: linear-gradient(160deg, #a12b3a 0%, var(--maroon) 45%, var(--maroon-deep) 100%);
    color: var(--white);
  }
  .card-front .facets { position: absolute; inset: 0; }
  .card-front .brand {
    position: absolute; right: 34px; top: 34px;
    text-align: right;
    color: var(--gold);
    font-weight: 600;
    font-size: 17px;
    letter-spacing: 1px;
    line-height: 1.25;
  }
  .card-front .divider {
    position: absolute; left: 150px; right: 34px; top: 112px;
    height: 1px; background: var(--rule);
  }
  .card-front .person { position: absolute; left: 40px; top: 128px; }
  .card-front .person-name { font-size: 24px; font-weight: 700; }
  .card-front .person-title { font-size: 15px; color: var(--gold); margin-top: 2px; }
  .card-front .contact {
    position: absolute; right: 34px; top: 128px;
    text-align: right; font-size: 14px; line-height: 1.5;
  }
  .card-front .address { color: var(--gold); margin-bottom: 4px; }
  .card-front .line { display: flex; justify-content: flex-end; align-items: center; gap: 8px; }
  .card-front .icon { width: 12px; height: 12px; }
  .card-front .email {
    position: absolute; right: 34px; bottom: 30px; font-size: 14px;
  }
  /* ---------- Back ---------- */
  .card-back {
    left: 620px; top: 300px;
    background: var(--paper);
  }
  .card-back .brand {
    position: absolute; left: 0; right: 0; top: 118px;
    text-align: center;
    color: var(--maroon);
    font-weight: 600;
    font-size: 26px;
    letter-spacing: 2px;
    line-height: 1.2;
  }
  .card-back .brand small { display: block; font-size: 26px; }
  .card-back .band-bottom {
    position: absolute; left: 0; right: 0; bottom: 0; height: 42px;
    background: var(--maroon);
    display: flex; align-items: center;
    padding-left: 26px;
    gap: 40px;
  }
  .card-back .website {
    color: var(--white); font-size: 17px; font-weight: 600; letter-spacing: 0.3px;
  }
  .card-back .band-top {
    position: absolute; right: 0; top: 26px; width: 120px; height: 26px;
    background: var(--maroon);
    display: flex; align-items: center; justify-content: center;
  }
  .arrows { display: block; }
</style>
</head>
<body>

  <section class="card card-front" aria-label="Business card front">
    <svg class="facets" width="540" height="310" viewBox="0 0 540 310">
      <polygon points="0,180 0,310 250,310" fill="var(--copper)" opacity="0.85"/>
      <polygon points="0,180 150,40 310,310 250,310" fill="var(--copper-light)" opacity="0.55"/>
      <polygon points="60,310 150,200 210,310" fill="var(--maroon-deep)" opacity="0.8"/>
    </svg>

    <div class="brand">HALLMOOR<br>SECURITY SYSTEMS INC.</div>
    <div class="divider"></div>

    <div class="person">
      <p class="person-name">Marcus Feldhaven</p>
      <p class="person-title">Owner</p>
    </div>

    <div class="contact">
      <p class="address">742 Larch Avenue<br>Dunmore, Ohio 44120</p>
      <p class="line">+555 2460-1180
        <svg class="icon" viewBox="0 0 12 12"><path d="M2 1h3l1 3-2 1a7 7 0 0 0 3 3l1-2 3 1v3c-6 0-9-3-9-9z" fill="none" stroke="var(--gold)" stroke-width="1.2"/></svg>
      </p>
      <p class="line">+5553140-77206
        <svg class="icon" viewBox="0 0 12 12"><rect x="3" y="1" width="6" height="10" rx="1" fill="none" stroke="var(--gold)" stroke-width="1.2"/></svg>
      </p>
      <p class="line">&nbsp;
        <svg class="icon" viewBox="0 0 12 12"><rect x="1" y="2.5" width="10" height="7" fill="none" stroke="var(--gold)" stroke-width="1.2"/><path d="M1 2.5l5 4 5-4" fill="none" stroke="var(--gold)" stroke-width="1.2"/></svg>
      </p>
    </div>

    <p class="email">info@marcusfeldhaven.com</p>
  </section>

  <section class="card card-back" aria-label="Business card back">
    <div class="band-top">
      <svg class="arrows" width="66" height="14" viewBox="0 0 66 14">
        <polygon points="14,0 0,7 14,14" fill="var(--gold)"/>
        <polygon points="38,0 24,7 38,14" fill="var(--gold)"/>
        <polygon points="62,0 48,7 62,14" fill="var(--gold)"/>
      </svg>
    </div>

    <div class="brand">HALLMOOR<small>SECURITY SYSTEMS INC.</small></div>

    <div class="band-bottom">
      <svg class="arrows" width="66" height="14" viewBox="0 0 66 14">
        <polygon points="0,0 14,7 0,14" fill="var(--gold)"/>
        <polygon points="24,0 38,7 24,14" fill="var(--gold)"/>
        <polygon points="48,0 62,7 48,14" fill="var(--gold)"/>
      </svg>
      <p class="website">www.hallmoorsecuritysystems.com</p>
    </div>
  </section>

</body>
</html>
```